Realty Group Needs Classy, Contemporary Letterhead Design

We need a letterhead design for a new realty company located in NY, USA. We buy investment properties to rehabilitate and or keep in our rental portfolio.

```html
<!DOCTYPE html>
<html lang="en">
<head>
<meta charset="utf-8">
<title>Meridian Realty Group – Letterhead</title>
<link href="https://fonts.googleapis.com/css2?family=Montserrat:wght@500;600&family=Source+Sans+3:wght@400;600&display=swap" rel="stylesheet">
<style>
  :root {
    --backdrop: #e2e2e2;
    --paper: #ffffff;
    --brand-purple: #4a2a86;
    --ink: #333333;
    --ink-dark: #111111;
    --band-grey: #808080;
  }
  * { box-sizing: border-box; margin: 0; padding: 0; }
  html, body {
    width: 1200px; height: 1200px; overflow: hidden;
    background: var(--backdrop);
  }
  .letterhead {
    position: absolute; left: 197px; top: 30px;
    width: 805px; height: 1140px;
    background: var(--paper);
    box-shadow: 0 4px 12px rgba(0,0,0,0.12);
    font-family: "Source Sans 3", "Myriad Pro", sans-serif;
    color: var(--ink);
  }
  .brand {
    position: absolute; top: 92px; left: 0; width: 100%;
    text-align: center;
    font-family: "Source Sans 3", sans-serif;
    font-weight: 600; font-size: 36px; line-height: 1;
    color: var(--brand-purple);
  }
  .recipient, .salutation, .letter-body {
    position: absolute; left: 75px;
    font-size: 16.5px; line-height: 21.7px;
    font-style: normal;
  }
  .recipient { top: 265px; }
  .salutation { top: 417px; }
  .letter-body { top: 460px; width: 655px; }
  .letter-body .line { display: block; white-space: nowrap; }
  .signature {
    position: absolute; left: 252px; top: 953px;
    width: 302px; height: 74px;
    background: linear-gradient(90deg, rgba(17,17,17,0.10), rgba(17,17,17,0.22), rgba(17,17,17,0.10));
    border-radius: 30px;
  }
  .footer-rule {
    position: absolute; left: 115px; top: 1036px;
    width: 575px; height: 2px; background: var(--brand-purple);
  }
  .footer-address {
    position: absolute; top: 1050px; left: 0; width: 100%;
    text-align: center;
    font-family: "Montserrat", sans-serif; font-weight: 600;
    font-size: 14.5px; color: var(--ink-dark);
  }
  .footer-contacts {
    position: absolute; top: 1078px; left: 0; width: 100%;
    display: flex; justify-content: center; gap: 10px;
    font-family: "Montserrat", sans-serif; font-weight: 500;
    font-size: 11.5px; color: var(--ink-dark);
  }
  .contact { display: flex; align-items: center; gap: 3px; white-space: nowrap; }
  .contact svg { width: 10px; height: 10px; }
  .bottom-band {
    position: absolute; left: 0; bottom: 0; width: 100%; height: 24px;
    background: var(--band-grey);
  }
</style>
</head>
<body>
  <main class="letterhead">
    <header class="brand">Meridian Realty Group, LLC</header>

    <address class="recipient">
      Mr. John Doe<br>
      President<br>
      Northfield Advisors<br>
      111 Street Name,<br>
      City State, 12345
    </address>

    <p class="salutation">Dear</p>

    <section class="letter-body">
      <span class="line">Lorem ipsum dolor sit amet, consectetur adipiscing elit. Aenean ut ipsum eget massa</span>
      <span class="line">hendrerit vestibulum vel in velit. Donec pretium neque velit.</span>
      <span class="line">Aliquam porta lectus nec mauris ornare venenatis. Vivamus non est turpis, et cursus sem.</span>
      <span class="line">Mauris vehicula erat in diam auctor at bibendum nisl lacinia.</span>
      <span class="line">Morbi imperdiet neque vehicula nunc convallis gravida. Vestibulum iaculis pretium placerat.</span>
      <span class="line">Integer consequat, est sit amet facilisis eleifend, nibh nibh varius orci, eget dapibus arcu dui</span>
      <span class="line">non purus. Pellentesque in magna mauris. Duis enim sapien, dictum vitae condimentum a,</span>
      <span class="line">pulvinar vel lacus. Mauris et molestie nibh. Vestibulum vitae nulla at metus elementum</span>
      <span class="line">porta sit amet interdum elit. Nulla sollicitudin neque eu nulla volutpat congue.</span>
      <span class="line">Etiam pellentesque, velit id dapibus fermentum, turpis sapien ornare dui, ac tincidunt ligula</span>
      <span class="line">odio congue purus. Nunc sed ante dui, in porta lectus. Cras nec sem lorem. In hac habitasse</span>
      <span class="line">platea dictumst. Maecenas id diam quis dui porta tristique. Sed id egestas felis. Donec</span>
      <span class="line">ullamcorper mattis posuere. Phasellus fermentum eleifend tortor vel dapibus. Vestibulum</span>
      <span class="line">ante ipsum.</span>
    </section>

    <div class="signature" role="img" aria-label="Handwritten signature of Daniel Rowe"></div>

    <div class="footer-rule"></div>
    <p class="footer-address">2150 Harbor View Ave, Suite 210 Albany NY 12207</p>

    <div class="footer-contacts">
      <span class="contact">
        <svg viewBox="0 0 10 10"><path d="M2 1 L4 3 L3 4 Q4 6 6 7 L7 6 L9 8 L8 9 Q3 9 1 2 Z" fill="var(--brand-purple)"/></svg>518.555.0142
      </span>
      <span class="contact">
        <svg viewBox="0 0 10 10"><rect x="2.5" y="0.5" width="5" height="9" rx="1" fill="none" stroke="var(--ink-dark)" stroke-width="0.9"/></svg>518.555.0187
      </span>
      <span class="contact">
        <svg viewBox="0 0 10 10"><rect x="3" y="1" width="4" height="3" fill="var(--brand-purple)"/><rect x="1" y="4" width="8" height="4" rx="1" fill="var(--brand-purple)"/></svg>518.555.0163
      </span>
      <span class="contact">
        <svg viewBox="0 0 10 10"><rect x="1" y="2" width="8" height="6" fill="var(--brand-purple)"/><path d="M1 2 L5 5.5 L9 2" stroke="#fff" stroke-width="0.8" fill="none"/></svg>daniel@meridianrealty.com
      </span>
      <span class="contact">
        <svg viewBox="0 0 10 10"><circle cx="5" cy="5" r="4" fill="none" stroke="var(--brand-purple)" stroke-width="0.9"/><ellipse cx="5" cy="5" rx="1.8" ry="4" fill="none" stroke="var(--brand-purple)" stroke-width="0.7"/><path d="M1 5 H9" stroke="var(--brand-purple)" stroke-width="0.7"/></svg>www.meridianrealty.com
      </span>
    </div>

    <div class="bottom-band"></div>
  </main>
</body>
</html>
```